New Business Card for Software Company

We are looking at rebranding a 10 year old company that specializes in PDF and DWF solutions for Architects and Engineers. We will attach the new company logo that we are going with so you can work with that and complimentary colors.
The sample information we would like on the business card is:
Gerald Pinfold
Vice President
4738 W. Harrowgate Lane. STE 305
PMB#417
Mesa, AZ 85374
866-392-5074 US Toll Free
123-456-3190 Cell
gpinfold@plavorix.com
The old tag line that we had on the business cars was.
Delivering Dependable PDF and DWF Tools for Architects and Engineers Around the World.
If you have an idea for a better tag line we are open to that also.
Updates
We would like to thank all of the Designers for their wonderful work. We apologize that we will not have the time to provide feedback to everyone. There is just so many innovative and professional designs that you have all created making our decision even harder.
Target Market(s)
Architects and Engineers
Industry/Entity Type
Business
Look and feel

```html
<!DOCTYPE html>
<html lang="en">
<head>
<meta charset="utf-8">
<title>Plavorix Business Card</title>
<link rel="stylesheet" href="https://fonts.googleapis.com/css2?family=Arimo:wght@400;700&family=PT+Sans&display=swap">
<style>
  :root {
    --bg: #e9e6e1;
    --card: #ffffff;
    --orange: #f2681e;
    --orange-light: #f7a12a;
    --red: #c8222a;
    --grey-dark: #555759;
    --grey: #6d6f71;
    --grey-light: #a7a9ab;
    --text: #333333;
  }
  * { box-sizing: border-box; margin: 0; padding: 0; }
  html, body { width: 1200px; height: 720px; overflow: hidden; }
  body {
    background: var(--bg);
    display: flex;
    align-items: center;
    justify-content: center;
    gap: 40px;
    font-family: "Arimo", Arial, sans-serif;
    color: var(--text);
  }
  .card {
    position: relative;
    width: 550px;
    height: 314px;
    background: var(--card);
    box-shadow: 0 4px 14px rgba(0,0,0,0.15);
    overflow: hidden;
  }
  /* Front */
  .brand {
    position: absolute;
    left: 34px;
    top: 30px;
    display: flex;
    align-items: center;
    gap: 12px;
  }
  .brand-dot {
    width: 52px; height: 52px;
    border-radius: 50%;
    background: var(--orange);
  }
  .brand-name {
    font-weight: 700;
    font-size: 50px;
    letter-spacing: -1px;
    color: var(--grey-dark);
    line-height: 1;
  }
  .person {
    position: absolute;
    left: 34px;
    top: 106px;
    width: 250px;
    text-align: right;
  }
  .person-name {
    font-weight: 700;
    font-size: 17px;
    color: var(--orange);
  }
  .person-title {
    font-size: 11px;
    color: var(--grey);
    margin-bottom: 6px;
  }
  .person-address {
    font-size: 12px;
    line-height: 1.35;
    color: var(--text);
    font-style: normal;
  }
  .divider {
    position: absolute;
    left: 298px;
    top: 104px;
    width: 1px;
    height: 76px;
    background: var(--grey-light);
  }
  .contacts {
    position: absolute;
    left: 312px;
    top: 104px;
    list-style: none;
    font-size: 12px;
    color: var(--text);
  }
  .contacts li {
    display: flex;
    align-items: center;
    gap: 8px;
    height: 24px;
  }
  .contacts svg { width: 11px; height: 11px; flex: none; }
  .swoosh {
    position: absolute;
    left: 0; top: 0;
    width: 550px; height: 314px;
  }
  /* Back */
  .card-back {
    display: flex;
    flex-direction: column;
    align-items: center;
    justify-content: center;
    gap: 34px;
  }
  .card-back .brand { position: static; gap: 16px; }
  .card-back .brand-dot { width: 70px; height: 70px; }
  .card-back .brand-name { font-size: 54px; }
  .tagline {
    font-family: "PT Sans", "Arimo", sans-serif;
    font-size: 15px;
    line-height: 1.3;
    text-align: center;
    color: var(--grey-dark);
  }
</style>
</head>
<body>

<section class="card card-front" aria-label="Business card front">
  <svg class="swoosh" viewBox="0 0 550 314" aria-hidden="true">
    <defs>
      <linearGradient id="band" x1="0" y1="1" x2="1" y2="0">
        <stop offset="0" stop-color="#f7a12a"/>
        <stop offset="0.45" stop-color="#f2681e"/>
        <stop offset="1" stop-color="#c8222a"/>
      </linearGradient>
    </defs>
    <path d="M0,270 C170,290 370,264 550,212 L550,314 L0,314 Z" fill="url(#band)"/>
    <path d="M0,258 C180,280 380,252 550,198" fill="none" stroke="#6d6f71" stroke-width="6"/>
    <path d="M0,292 C180,306 380,284 550,244 L550,314 L0,314 Z" fill="#f2681e" opacity="0.55"/>
  </svg>

  <div class="brand">
    <span class="brand-dot"></span>
    <span class="brand-name">Plavorix</span>
  </div>

  <div class="person">
    <div class="person-name">Gerald Pinfold</div>
    <div class="person-title">Vice President</div>
    <address class="person-address">4738 W. Harrowgate Lane. STE 305<br>PMB#417, Mesa, AZ 85374</address>
  </div>

  <span class="divider"></span>

  <ul class="contacts">
    <li>
      <svg viewBox="0 0 12 12" aria-hidden="true"><circle cx="6" cy="6" r="6" fill="#f2681e"/><path d="M4,3 L5,3 L5.5,4.6 L4.8,5.2 C5.2,6 6,6.8 6.8,7.2 L7.4,6.5 L9,7 L9,8 C6,8.5 3.5,6 4,3 Z" fill="#fff"/></svg>
      866-392-5074 (US) TF
    </li>
    <li>
      <svg viewBox="0 0 12 12" aria-hidden="true"><circle cx="6" cy="6" r="6" fill="#f2681e"/><rect x="4.2" y="2.5" width="3.6" height="7" rx="0.6" fill="#fff"/><rect x="4.8" y="3.3" width="2.4" height="4.2" fill="#f2681e"/></svg>
      123-456-3190
    </li>
    <li>
      <svg viewBox="0 0 12 12" aria-hidden="true"><circle cx="6" cy="6" r="6" fill="#f2681e"/><rect x="3" y="4" width="6" height="4.2" fill="#fff"/><path d="M3,4 L6,6.4 L9,4" fill="none" stroke="#f2681e" stroke-width="0.7"/></svg>
      gpinfold@plavorix.com
    </li>
  </ul>
</section>

<section class="card card-back" aria-label="Business card back">
  <div class="brand">
    <span class="brand-dot"></span>
    <span class="brand-name">Plavorix</span>
  </div>
  <p class="tagline">Delivering Dependable PDF and DWF Tools for Architects<br>and Engineers Around the World</p>
</section>

</body>
</html>
```